Coastline Premier Retreats Business Card Design

Design a business card for Coastline Premier Retreats. Look at the website for colors and reference. Card should have logo, name, title, office number, mobile number, email, URL and a tagline like, "Luxury Hotel & Resort Email Marketing" (This might change).

https://www.coastlinepremierretreats.example

The rest I will leave up to your imagination.

Contact Information for Business Card

Logo, name, title, office number, mobile number, email, URL and a tagline like, "Luxury Hotel & Resort Email Marketing" (This might change).

```html
<!DOCTYPE html>
<html lang="en">
<head>
<meta charset="utf-8">
<title>Coastline Premier Retreats – Business Card</title>
<link href="https://fonts.googleapis.com/css2?family=Montserrat:ital,wght@0,400;0,500;0,700;0,800;1,400&display=swap" rel="stylesheet">
<style>
  :root {
    --stage: #2b2b2b;
    --card: #1a1a1a;
    --orange: #ef7317;
    --white: #ffffff;
  }
  * { box-sizing: border-box; margin: 0; padding: 0; }
  html, body {
    width: 1200px; height: 1200px; overflow: hidden;
    background: var(--stage);
    font-family: "Montserrat", sans-serif;
  }
  .stage {
    position: relative; width: 1200px; height: 1200px;
    display: flex; justify-content: center; align-items: center; gap: 60px;
  }
  .card {
    position: relative; width: 420px; height: 720px;
    background: var(--card);
    box-shadow: 0 18px 40px rgba(0,0,0,0.45);
    overflow: hidden;
  }
  /* Front */
  .front .brand-name {
    position: absolute; top: 120px; left: 0; right: 0;
    text-align: center;
    color: var(--white); font-weight: 700;
    font-size: 26px; line-height: 1.25; letter-spacing: 0.06em;
    text-transform: uppercase;
  }
  .front .accent-bar {
    position: absolute; left: 0; top: 440px;
    width: 22px; height: 48px; background: var(--orange);
  }
  .front .holder {
    position: absolute; left: 52px; top: 438px;
  }
  .holder .person-name {
    color: var(--orange); font-weight: 800; font-size: 30px;
    letter-spacing: 0.04em; text-transform: uppercase; line-height: 1;
  }
  .holder .person-title {
    color: var(--white); font-size: 17px; font-weight: 400;
    margin-top: 6px; letter-spacing: 0.03em;
  }
  .contacts {
    position: absolute; left: 30px; top: 560px; list-style: none;
  }
  .contacts li {
    display: flex; align-items: center; gap: 10px;
    color: var(--white); font-size: 16px; letter-spacing: 0.02em;
    margin-bottom: 12px; white-space: nowrap;
  }
  .contacts .label { color: var(--orange); font-size: 12px; }
  .contacts svg { width: 16px; height: 16px; flex: none; }
  /* Back */
  .back .rotated {
    position: absolute; left: 50%; top: 50%;
    transform: translate(-50%, -50%) rotate(-90deg);
    white-space: nowrap; text-align: center;
  }
  .back .brand-name {
    color: var(--white); font-weight: 700; font-size: 36px;
    letter-spacing: 0.06em; text-transform: uppercase;
  }
  .back .tagline {
    position: absolute; left: 76%; top: 50%;
    transform: translate(-50%, -50%) rotate(-90deg);
    white-space: nowrap;
    color: var(--orange); font-size: 18px; font-style: italic; font-weight: 400;
  }
</style>
</head>
<body>
<main class="stage">
  <section class="card front">
    <p class="brand-name">Coastline<br>Premier Retreats</p>
    <div class="accent-bar"></div>
    <div class="holder">
      <h1 class="person-name">Daniel Hayes</h1>
      <p class="person-title">Managing Director</p>
    </div>
    <ul class="contacts">
      <li>
        <svg viewBox="0 0 16 16" aria-hidden="true"><rect x="4" y="1" width="8" height="14" rx="1.5" fill="none" stroke="#ef7317" stroke-width="1.5"/><line x1="7" y1="12.5" x2="9" y2="12.5" stroke="#ef7317" stroke-width="1.5"/></svg>
        <span>555.014.2387</span><span class="label">(Mobile)</span>
      </li>
      <li>
        <svg viewBox="0 0 16 16" aria-hidden="true"><path d="M2 6c0-2 2.5-3.5 6-3.5S14 4 14 6l-3 .5V5H5v1.5z" fill="#ef7317"/><rect x="3" y="8" width="10" height="6" rx="1" fill="#ef7317"/></svg>
        <span>555.014.6000</span><span class="label">(Office)</span>
      </li>
      <li>
        <svg viewBox="0 0 16 16" aria-hidden="true"><rect x="1" y="3.5" width="14" height="9" fill="#ef7317"/><path d="M1 3.5l7 5 7-5" fill="none" stroke="#1a1a1a" stroke-width="1.2"/></svg>
        <span>dhayes@coastlinepremierretreats.net</span>
      </li>
    </ul>
  </section>

  <section class="card back">
    <div class="rotated">
      <p class="brand-name">Coastline Premier Retreats</p>
    </div>
    <p class="tagline">Luxury Hotel &amp; Resort Email Marketing</p>
  </section>
</main>
</body>
</html>
```